Tollin Waste Website Design

Our new start-up needs a website design. We plan to help businesses find more sustainable ways to manage their waste. Our initial website aims to gather contact data from potential business customers and comprehensive information from waste facilities and waste transporters. We have a logo design (attached) which we would like included in the website design. I have also attached a number of pages that describe what information should appear on each page as well as a web design brief file that describes the look we are after.

```html
<!DOCTYPE html>
<html lang="en">
<head>
<meta charset="utf-8">
<title>Tollin Waste</title>
<link href="https://fonts.googleapis.com/css2?family=Urbanist:wght@400;500;600;700&display=swap" rel="stylesheet">
<style>
  :root{
    --green:#6fa334;
    --green-deep:#5e8f2a;
    --ink:#333333;
    --white:#ffffff;
    --page-grey:#f2f2f2;
    --footer:#000000;
    --shade:rgba(0,0,0,0.42);
  }
  *{box-sizing:border-box;margin:0;padding:0}
  html,body{width:1200px;height:1120px;overflow:hidden}
  body{position:relative;font-family:"Urbanist",sans-serif;background:var(--page-grey)}
  .hero{position:absolute;left:0;top:0;width:1200px;height:622px;
    background:linear-gradient(180deg,#5f6876 0%,#7a8390 45%,#c8ccd0 100%)}
  .brand{position:absolute;left:71px;top:40px;display:flex;align-items:center;gap:12px;
    color:var(--white);font-weight:700;font-size:34px;letter-spacing:1px}
  .brand-dot{width:40px;height:40px;border-radius:50%;background:var(--green)}
  .nav a{position:absolute;top:54px;color:var(--white);font-size:17px;font-weight:500;text-decoration:none}
  .search{position:absolute;left:1109px;top:55px}
  .slide-btn{position:absolute;top:321px;width:48px;height:48px;border-radius:50%;display:flex;align-items:center;justify-content:center}
  .slide-btn.prev{left:24px;background:#333}
  .slide-btn.next{left:1127px;background:var(--green)}
  .services{position:absolute;left:66px;top:487px;width:1066px;height:356px;background:var(--green)}
  .card{position:absolute;top:61px;width:335px;height:235px;border:2px solid rgba(255,255,255,0.7);
    display:flex;flex-direction:column;align-items:center;justify-content:flex-end;padding-bottom:54px;
    color:var(--white);font-size:25px;font-weight:600}
  .card.mid{background:var(--white);color:var(--green);border-color:var(--white)}
  .card-icon{width:80px;height:44px;margin-bottom:18px;background:rgba(255,255,255,0.35);border-radius:4px}
  .card.mid .card-icon{background:rgba(111,163,52,0.35)}
  .footer{position:absolute;left:0;top:896px;width:1200px;height:224px;background:var(--footer);color:var(--white);text-align:center}
  .social{position:absolute;top:54px;width:32px;height:32px;border:1.5px solid var(--white);border-radius:50%}
  .foot-nav a{position:absolute;top:114px;transform:translateX(-50%);color:var(--white);font-size:17px;font-weight:600;text-decoration:none}
  .legal{position:absolute;top:152px;width:100%;font-size:16px;font-weight:500}
  .shade{position:absolute;inset:0;background:var(--shade)}
  .modal{position:absolute;left:119px;top:236px;width:953px;height:408px;background:var(--white);border-radius:18px;text-align:center}
  .close{position:absolute;left:897px;top:29px}
  .modal h1{margin-top:76px;color:var(--green);font-size:44px;font-weight:700}
  .modal p{margin:22px auto 0;width:740px;color:var(--ink);font-size:21px;line-height:35px;font-weight:500}
  .signup{position:absolute;left:226px;top:257px;width:502px;height:67px;border:1.5px solid #9a9a9a;border-radius:34px}
  .signup input{position:absolute;left:16px;top:0;height:64px;width:260px;border:none;background:none;outline:none;
    font-family:inherit;font-size:16px;color:#555}
  .signup input::placeholder{color:#555}
  .signup button{position:absolute;right:-2px;top:-1.5px;width:200px;height:67px;border:none;border-radius:34px;
    background:var(--green);color:var(--white);font-family:inherit;font-size:21px;font-weight:700}
</style>
</head>
<body>
  <div class="hero" role="img" aria-label="Photo of a white refuse collection truck under a cloudy sky"></div>
  <div class="brand"><span class="brand-dot"></span>Tollin Waste</div>
  <nav class="nav">
    <a style="left:548px">Home</a><a style="left:633px">About Us</a><a style="left:742px">What We do</a>
    <a style="left:877px">Resources</a><a style="left:998px">Contact Us</a>
  </nav>
  <svg class="search" width="18" height="18" viewBox="0 0 18 18"><circle cx="7.5" cy="7.5" r="5.5" fill="none" stroke="#fff" stroke-width="2.4"/><line x1="11.5" y1="11.5" x2="16" y2="16" stroke="#fff" stroke-width="2.6" stroke-linecap="round"/></svg>
  <div class="slide-btn prev"><svg width="14" height="18" viewBox="0 0 14 18"><path d="M9 3 L4 9 L9 15" fill="none" stroke="#fff" stroke-width="2"/></svg></div>
  <div class="slide-btn next"><svg width="14" height="18" viewBox="0 0 14 18"><path d="M5 3 L10 9 L5 15" fill="none" stroke="#fff" stroke-width="2"/></svg></div>

  <section class="services">
    <div class="card" style="left:21px"><div class="card-icon" role="img" aria-label="Waste producers icon"></div>Waste Producers</div>
    <div class="card mid" style="left:366px"><div class="card-icon" role="img" aria-label="Waste facilities icon"></div>Waste Facilities</div>
    <div class="card" style="left:710px"><div class="card-icon" role="img" aria-label="Waste transporters icon"></div>Waste Transporters</div>
  </section>

  <footer class="footer">
    <span class="social" style="left:532px"></span><span class="social" style="left:572px"></span><span class="social" style="left:612px"></span>
    <nav class="foot-nav">
      <a style="left:286px">Home</a><a style="left:417px">About Us</a><a style="left:572px">What We do</a>
      <a style="left:734px">Resources</a><a style="left:891px">Contact Us</a>
    </nav>
    <div class="legal">Copyright 2018 | All rights reserved | Privacy Policy | Term &amp; Conditions</div>
  </footer>

  <div class="shade"></div>

  <div class="modal">
    <svg class="close" width="30" height="30" viewBox="0 0 30 30"><circle cx="15" cy="15" r="13" fill="none" stroke="#000" stroke-width="2.5"/><path d="M10 10 L20 20 M20 10 L10 20" stroke="#000" stroke-width="2.5"/></svg>
    <h1>Welcome to Tollin Waste</h1>
    <p>We are just getting started. Please register your email address to receive updates from us.</p>
    <form class="signup">
      <input type="email" placeholder="enter your email address">
      <button type="button">Submit</button>
    </form>
  </div>
</body>
</html>
```